Online Advice via Video Site requires Cutting Edge Homepage

We need a creative new and exciting webdesign for our tutoring via video-chat website.

We have prepared a "demo" homepage for you to see various promotional material that we think would be suitable for the homepage. http://www.quillmarsh.com/demo

The actual site is undergoing some final tinkering but can be accessed and used at http://www.quillmarsh.com

There is NO NEED to take any colours or design structure from this.

We expect the logo to be changed to match the new site. The new logo should match the site's function.

I have included some other projects that we like the look of:
http://www.vantoplex.com.au/design/143762
http://www.vantoplex.com.au/design/561630
http://www.vantoplex.com.au/design/247199
http://www.vantoplex.com.au/design/255195
http://www.birchlume.tv/

Target Market(s)

People that will work as tutors/advisers or be student/clients

Industry/Entity Type

Tutoring

Requirements
Must have
• The search is the main feature of the homepage

After the search the next goal of the page is to get people to sign up to the site

Login, (optional inclusion of the gablenet login - if you don't include it then you need only have a "login" button... no username or password input fields)

Footer
Nice to have
• The promotional material for the site, the colours on the Prezi file CAN BE changed to suit the new design you propose.

```html
<!DOCTYPE html>
<html lang="en">
<head>
<meta charset="utf-8">
<title>Quill Marsh — Homepage</title>
<link rel="stylesheet" href="https://fonts.googleapis.com/css2?family=Open+Sans:wght@400;600&family=Noto+Serif:wght@400;700&display=swap">
<style>
:root{
  --navy:#1d3f8f;
  --navy-dark:#163577;
  --blue-text:#2a3fa0;
  --orange:#f39a12;
  --orange-dark:#e07f05;
  --sky:#e8eefb;
  --line:#c7d0e2;
  --grey-text:#666;
  --footer-bg:#f2f2f2;
  --bar-bg:#3a3a3a;
}
*{margin:0;padding:0;box-sizing:border-box}
html,body{width:835px;height:1200px;overflow:hidden}
body{position:relative;font-family:Arial,Helvetica,sans-serif;background:linear-gradient(#e6ecfa 0,#f7f9fe 170px,#fff 430px,#fff);color:#333}
.abs{position:absolute}
.top-rule{left:0;top:0;width:835px;height:3px;background:var(--navy)}

/* login */
.login-panel{left:478px;top:0;width:305px;height:48px;background:var(--navy);border-radius:0 0 4px 4px;box-shadow:0 3px 6px rgba(0,0,0,.25)}
.login-panel svg{position:absolute;left:8px;top:15px}
.login-field{position:absolute;top:19px;height:18px;background:#fff;border:1px solid #9fb0d8;font:10px 'Open Sans',sans-serif;color:#7a8bb5;padding:2px 6px}
.login-field.user{left:33px;width:104px}
.login-field.pass{left:141px;width:103px}
.signin-btn{position:absolute;left:248px;top:17px;width:49px;height:21px;background:linear-gradient(var(--orange),var(--orange-dark));border-radius:3px;color:#fff;font:10px 'Open Sans',sans-serif;text-align:center;line-height:21px}

/* brand */
.brand{left:28px;top:56px;font:400 27px 'Open Sans',sans-serif;color:#2a4f9c;letter-spacing:-.3px}

/* search */
.search-box{left:257px;top:78px;width:240px;height:29px;background:#fff;border:1px solid #c5cfe4;font:11px 'Open Sans',sans-serif;color:#333;padding:6px 11px}
.search-btn{left:497px;top:78px;width:74px;height:29px;background:var(--orange);color:#fff;font:12px 'Open Sans',sans-serif;text-align:center;line-height:29px}
.gablenet-login{left:683px;top:84px;width:100px;height:20px;background:linear-gradient(#6f8fce,#3e62ae);color:#fff;font:10px 'Open Sans',sans-serif;line-height:20px;padding-left:28px}
.gablenet-login::before{content:"";position:absolute;left:2px;top:2px;width:16px;height:16px;background:#2d4f96}

/* nav */
.main-nav{left:13px;top:135px;width:798px;height:34px;background:linear-gradient(#fff,#eef1f7);border:1px solid #b8c6e0;display:flex}
.main-nav a{display:block;height:32px;line-height:32px;text-align:center;font:12.5px 'Open Sans',sans-serif;color:var(--navy);text-decoration:none;border-right:1px solid #c8d2e6}
.main-nav a:last-child{border-right:none}
.main-nav a.active{background:linear-gradient(#2452b2,#17388a);color:#fff}

/* hero */
.hero{left:13px;top:178px;width:798px;height:247px;background:#f4f6fa;border:1px solid #dde3ee;box-shadow:0 6px 8px -4px rgba(0,0,0,.2);overflow:hidden}
.hero-photo{position:absolute;left:360px;top:0;width:438px;height:247px;background:linear-gradient(90deg,#f4f6fa 0,#e6ebf1 15%,#c9d2de 45%,#8a8f98 72%,#4b4d52 100%)}
.hero-title{position:absolute;left:30px;top:32px;width:350px;font:400 16.5px/23px 'Noto Serif',serif;color:#1d3566}
.hero-copy{position:absolute;left:29px;top:109px;width:350px;font:9.2px/16px 'Open Sans',sans-serif;color:#777}
.join-btn{position:absolute;left:28px;top:167px;width:103px;height:20px;background:linear-gradient(var(--orange),var(--orange-dark));border-radius:2px;color:#fff;font:600 10px/20px 'Open Sans',sans-serif;text-align:center}

/* welcome */
.section-title{font:15px Arial,Helvetica,sans-serif;color:var(--navy)}
.welcome-title{left:21px;top:451px}
.welcome-copy{left:21px;top:479px;width:518px;font:10.3px/18px Arial,Helvetica,sans-serif;color:var(--blue-text)}
.welcome-copy p{margin-bottom:6px}

/* featured */
.featured-title{left:558px;top:450px}
.service{left:552px;width:268px;height:52px;background:linear-gradient(90deg,#f1f4fc,#e4eafa 70%,#f6f8fe);border-bottom:1px solid #fff}
.service svg{position:absolute;left:16px;top:12px}
.service h3{position:absolute;left:56px;top:6px;font:400 11.5px 'Open Sans',sans-serif;color:var(--navy)}
.service p{position:absolute;left:56px;top:22px;width:195px;font:8.3px/11.5px 'Open Sans',sans-serif;color:#333}

/* three columns */
.col-title{top:675px}
.col-rule{top:698px;height:1px;background:var(--line)}
.why-photo{left:18px;top:711px;width:201px;height:79px;background:linear-gradient(90deg,#f3f4f6,#e6d9cf 45%,#c9ccd2 75%,#a8adb5);border:1px solid #dde1e8}
.why-copy{left:19px;top:796px;width:200px;font:8.8px/15px 'Open Sans',sans-serif;color:#444}
.why-links{left:19px;top:850px;list-style:none;width:210px}
.why-links li{position:relative;padding-left:13px;font:8.8px/16px 'Open Sans',sans-serif;color:#333;text-decoration:underline;margin-bottom:8px}
.why-links li::before{content:"";position:absolute;left:1px;top:5px;width:5px;height:5px;background:var(--navy)}
.video{left:256px;top:711px;width:275px;height:190px;background:#1c1c1c;box-shadow:0 8px 8px -3px rgba(0,0,0,.35)}
.video-bar{position:absolute;left:0;bottom:0;width:275px;height:14px;background:linear-gradient(#555,#2a2a2a)}
.tweet{left:569px;width:235px;font:8.8px/16px 'Open Sans',sans-serif;color:#444}
.tweet-date{display:block;color:var(--navy);font-size:9.5px;margin-top:5px}
.tweet-rule{left:566px;top:809px;width:241px;border-top:1px dotted #999}

/* footer */
.footer{left:0;top:950px;width:835px;height:202px;background:var(--footer-bg)}
.footer-col{position:absolute;top:20px}
.footer-col h4{font:400 12.5px 'Open Sans',sans-serif;color:#444;margin-bottom:12px}
.footer-col li{list-style:none;font:8.3px 'Open Sans',sans-serif;color:#444;margin-bottom:9.5px}
.footer-divider{position:absolute;top:0;height:170px;border-left:1px dotted #bbb}
.social-squares{display:flex;gap:2px;margin-bottom:4px}
.social-squares span{width:14px;height:14px;display:block}
.social-names{font:8.3px 'Open Sans',sans-serif;color:#444}
.bottom-bar{left:0;top:1152px;width:835px;height:48px;background:var(--bar-bg);font:9.3px 'Open Sans',sans-serif;color:#ccc}
.bottom-bar span{position:absolute;top:16px}
</style>
</head>
<body>
<div class="abs top-rule"></div>

<div class="abs login-panel">
  <svg width="18" height="22" viewBox="0 0 18 22" aria-hidden="true"><circle cx="9" cy="6" r="5" fill="#fff"/><path d="M0 21c0-6 4-9 9-9s9 3 9 9z" fill="#fff"/></svg>
  <div class="login-field user">username</div>
  <div class="login-field pass">password</div>
  <div class="signin-btn">Sing In</div>
</div>

<div class="abs brand">Quill Marsh</div>

<div class="abs search-box">type here for Search</div>
<div class="abs search-btn">SEARCH</div>
<div class="abs gablenet-login">LOG IN NOW</div>

<nav class="abs main-nav">
  <a class="active" style="width:97px">Main</a>
  <a style="width:109px">About us</a>
  <a style="width:105px">Services</a>
  <a style="width:109px">Partners</a>
  <a style="width:130px">Testimonials</a>
  <a style="width:106px">Videos</a>
  <a style="width:140px">Contact</a>
</nav>

<section class="abs hero">
  <div class="hero-photo" role="img" aria-label="Photo of a smiling woman in glasses with colleagues working at a laptop in a bright office"></div>
  <h1 class="hero-title">Imagine if, whenever you had a problem you could instantly access the world's experts to solve it. Now you can!"</h1>
  <p class="hero-copy">E-Commerce is a major progress in technology that has changed the way in which the customers now purchase information, products and the services. It's the new way of providing an opportunity to make your products</p>
  <div class="join-btn">JOIN NOW US</div>
</section>

<h2 class="abs section-title welcome-title">Welcome to Our Website Mainpage</h2>
<div class="abs welcome-copy">
  <p>Brightvale Webworks is a professional website design company dedicated to provide excellent services. We at Brightvale Webworks think graphic design as a combination and collaboration of ideas and technology. Our Website Design team give an unforgettable impression on the customers and the clients. We can assure you that this is the best place for requirement of yours regarding website design solutions</p>
  <p>&nbsp;Brightvale Webworks provides you the Search Engine Optimization making your website search engine friendly.</p>
  <p>So that the website can achieve top position and ranking in the Internet searches and thereby increasing the scope for the website to be found by customers. We here modify the site to improve the ranking by using the keywords and contents.</p>
</div>

<h2 class="abs section-title featured-title">Featured Services</h2>
<div class="abs service" style="top:476px">
  <svg width="26" height="24" viewBox="0 0 26 24" aria-hidden="true"><rect x="1" y="14" width="5" height="8" fill="#f28a1e"/><rect x="8" y="9" width="5" height="13" fill="#e2462b"/><rect x="15" y="4" width="5" height="18" fill="#f28a1e"/><rect x="0" y="22" width="24" height="1.5" fill="#2c62b8"/></svg>
  <h3>First Service here</h3>
  <p>It's the new way of providing an opportunity to make your products and services available</p>
</div>
<div class="abs service" style="top:529px">
  <svg width="26" height="26" viewBox="0 0 26 26" aria-hidden="true"><circle cx="13" cy="13" r="10" fill="none" stroke="#7cbf2a" stroke-width="5"/></svg>
  <h3>Second Service here</h3>
  <p>It's the new way of providing an opportunity to make your products and services available</p>
</div>
<div class="abs service" style="top:583px">
  <svg width="26" height="26" viewBox="0 0 26 26" aria-hidden="true"><circle cx="13" cy="13" r="11" fill="#f28a1e"/><path d="M13 13V2a11 11 0 0 1 11 11z" fill="#3a6fc4"/></svg>
  <h3>Thrid Service here</h3>
  <p>It's the new way of providing an opportunity to make your products and services available</p>
</div>

<h2 class="abs section-title col-title" style="left:22px">Why We Are ?</h2>
<div class="abs col-rule" style="left:18px;width:210px"></div>
<h2 class="abs section-title col-title" style="left:254px">Watch Our Latest Videos !</h2>
<div class="abs col-rule" style="left:254px;width:277px"></div>
<h2 class="abs section-title col-title" style="left:566px">Recent Tweet Blog</h2>
<div class="abs col-rule" style="left:564px;width:243px"></div>

<div class="abs why-photo" role="img" aria-label="Photo of a young woman looking upward with colleagues behind her"></div>
<p class="abs why-copy">Brightvale Webworks is a professional website design company dedicated to provide excellent services.</p>
<ul class="abs why-links">
  <li>Brightvale Webworks think graphic design as a combination</li>
  <li>Brightvale Webworks design combination</li>
</ul>

<div class="abs video">
  <svg class="abs" style="left:125px;top:73px" width="28" height="32" viewBox="0 0 28 32" aria-hidden="true"><path d="M0 0L28 16L0 32z" fill="#fff"/></svg>
  <div class="video-bar">
    <svg width="275" height="14" viewBox="0 0 275 14" aria-hidden="true"><path d="M6 4l5 3-5 3z" fill="#ccc"/><rect x="18" y="6" width="150" height="2" fill="#888"/><circle cx="22" cy="7" r="3" fill="#ddd"/><text x="180" y="10" font-size="7" fill="#6cf" font-family="Arial">00:00</text><text x="200" y="10" font-size="7" fill="#ccc" font-family="Arial">04:52</text><rect x="226" y="5" width="14" height="4" fill="#999"/><rect x="260" y="4" width="7" height="6" fill="none" stroke="#ccc"/></svg>
  </div>
</div>

<div class="abs tweet" style="top:706px">
  <p>Brightvale Webworks is a professional website design company dedicated to provide excellent services.</p>
  <p style="margin-top:7px">We at Brightvale Webworks think graphic design as a combination and collaboration of ideas and technology.</p>
  <span class="tweet-date">March 05 2011</span>
</div>
<div class="abs tweet-rule"></div>
<div class="abs tweet" style="top:823px">
  <p>We at Brightvale Webworks think graphic design as a combination and collaboration of ideas and technology.</p>
  <span class="tweet-date">March 01 2011</span>
</div>

<footer class="abs footer">
  <div class="footer-divider" style="left:145px"></div>
  <div class="footer-divider" style="left:285px"></div>
  <div class="footer-divider" style="left:432px"></div>
  <div class="footer-divider" style="left:609px"></div>
  <div class="footer-col" style="left:29px"><h4>Company</h4><ul><li>Mainpage</li><li>Overview</li><li>About Our Company</li><li>Services</li><li>Partners</li></ul></div>
  <div class="footer-col" style="left:172px"><h4>Services List</h4><ul><li>Business Services</li><li>Direct Videos</li><li>Advisors and Clients</li><li>Personal Advice</li></ul></div>
  <div class="footer-col" style="left:315px"><h4>Support &amp; FAQ</h4><ul><li>Agriculture</li><li>Buidling</li><li>Veterinary Science</li><li>Cultural Studies</li><li>Criminology</li></ul></div>
  <div class="footer-col" style="left:470px;top:23px"><h4>More Services</h4><ul><li>Quill Marsh First Services</li><li>Quill Marsh Second Services</li><li>Thrid Second Services</li><li>Fourth Second Services</li></ul></div>
  <div class="footer-col" style="left:640px;top:23px"><h4>Get In Touch</h4>
    <div class="social-squares"><span style="background:#4aa3df"></span><span style="background:#2a6aa8"></span><span style="background:#3b5a9a"></span><span style="background:#4f7fd4"></span></div>
    <p class="social-names">Chirpline &nbsp;|&nbsp; Linkwell &nbsp;|&nbsp; Gablenet &nbsp;|&nbsp; Searchly</p>
  </div>
</footer>

<div class="abs bottom-bar">
  <span style="left:24px">Copyright © 2012 Company Name &nbsp;|&nbsp; All right reserved</span>
  <span style="left:574px">Copyright © 2012 Company Name &nbsp;|&nbsp; All right reserved</span>
</div>
</body>
</html>
```